Veldmark Supplies Business Card

Professional business card that stand out to our potential customers. Front and back with clean modern design

Industry/Entity Type

Oil and gas

Contact Information for Business Card

Name, address, website , office phone and cell number

Requirements
Must have
• Editable files for each employee

```html
<!DOCTYPE html>
<html lang="en">
<head>
<meta charset="utf-8">
<title>Veldmark Supplies Business Card</title>
<link rel="stylesheet" href="https://fonts.googleapis.com/css2?family=Montserrat:wght@400;500;700;800&display=swap">
<style>
  :root {
    --bg: #1e1e1f;
    --card: #2a2a2b;
    --card-edge: #333334;
    --red: #e8202a;
    --blue: #12b3d6;
    --white: #f2f2f2;
  }
  * { box-sizing: border-box; margin: 0; padding: 0; }
  html, body {
    width: 1200px; height: 689px; overflow: hidden;
    background: var(--bg);
    font-family: "Montserrat", sans-serif;
  }
  .canvas {
    position: relative; width: 1200px; height: 689px;
    display: flex; align-items: center; justify-content: center; gap: 40px;
  }
  .card {
    position: relative;
    width: 540px; height: 310px;
    border-radius: 16px;
    background: var(--card);
    box-shadow: 0 0 0 1px var(--card-edge);
    overflow: hidden;
  }
  /* Back side */
  .card-back .pattern-field {
    position: absolute; inset: 0;
    background: linear-gradient(120deg, #2a9bb8 0%, #6f8a92 35%, #a8685a 65%, #d9392c 100%);
    opacity: 0.55;
  }
  .card-back .center-mark {
    position: absolute; right: 150px; top: 118px;
    width: 22px; height: 22px; background: var(--red);
  }
  /* Front side */
  .card-front .brand {
    position: absolute; left: 0; top: 0; bottom: 0; width: 268px;
    display: flex; align-items: center; justify-content: center; gap: 12px;
    padding: 0 20px;
  }
  .brand-square { width: 26px; height: 26px; background: var(--red); flex: none; }
  .brand-name {
    font-weight: 800; font-size: 22px; line-height: 1.1; letter-spacing: 0.5px;
    color: var(--red); text-transform: uppercase;
  }
  .brand-name span { display: block; }
  .divider {
    position: absolute; left: 268px; top: 44px;
    width: 2px; height: 222px; background: var(--red);
  }
  .contact {
    position: absolute; left: 290px; top: 44px; right: 16px;
    color: var(--white);
  }
  .person-name {
    font-weight: 800; font-size: 21px; color: var(--red);
    text-transform: uppercase; letter-spacing: 0.3px; line-height: 1.1;
  }
  .person-title { font-size: 12px; font-weight: 500; margin-top: 4px; }
  .address { font-size: 12px; font-weight: 500; margin-top: 14px; line-height: 1.4; }
  .contact-list { list-style: none; margin-top: 14px; }
  .contact-list li {
    display: flex; align-items: center; gap: 9px;
    font-size: 12px; font-weight: 500; line-height: 1; margin-bottom: 9px;
    white-space: nowrap;
  }
  .icon {
    width: 16px; height: 16px; background: var(--red); border-radius: 2px;
    display: flex; align-items: center; justify-content: center; flex: none;
  }
  .icon svg { width: 11px; height: 11px; }
</style>
</head>
<body>
<main class="canvas">
  <section class="card card-back" aria-label="Card back">
    <div class="pattern-field" role="img" aria-label="Repeating brand-mark pattern fading from blue to red"></div>
    <div class="center-mark"></div>
  </section>

  <section class="card card-front" aria-label="Card front">
    <div class="brand">
      <span class="brand-square"></span>
      <span class="brand-name"><span>Veldmark</span><span>Supplies</span></span>
    </div>
    <div class="divider"></div>
    <div class="contact">
      <h1 class="person-name">Orlen Vasquet</h1>
      <p class="person-title">President</p>
      <p class="address">4620 Harrow Ridge Rd, Ste<br>210, Corvale, TX 75840</p>
      <ul class="contact-list">
        <li><span class="icon"><svg viewBox="0 0 12 12"><path d="M2 4c0-1 1-2 4-2s4 1 4 2v1H8V4H4v1H2z M3 6h6l1 4H2z" fill="#fff"/></svg></span>555-214-7093</li>
        <li><span class="icon"><svg viewBox="0 0 12 12"><rect x="3" y="1" width="6" height="10" rx="1" fill="none" stroke="#fff" stroke-width="1.3"/><circle cx="6" cy="9" r="0.7" fill="#fff"/></svg></span>000-000-9999</li>
        <li><span class="icon"><svg viewBox="0 0 12 12"><rect x="1" y="3" width="10" height="7" fill="none" stroke="#fff" stroke-width="1.2"/><path d="M1 3l5 4 5-4" fill="none" stroke="#fff" stroke-width="1.2"/></svg></span>info@example-youremail.com</li>
        <li><span class="icon"><svg viewBox="0 0 12 12"><circle cx="6" cy="6" r="4.5" fill="none" stroke="#fff" stroke-width="1.2"/><path d="M1.5 6h9M6 1.5c-2 2.5-2 6.5 0 9M6 1.5c2 2.5 2 6.5 0 9" fill="none" stroke="#fff" stroke-width="1"/></svg></span>www.example-yourwebsite.com</li>
      </ul>
    </div>
  </section>
</main>
</body>
</html>
```